Corporate brochure design 4 pages

Hi,

We are a real estate company based in Europe.

We have almost finalized a rebranding.

We are developing a brand book guidelines (still on working process) to help you undertstand the look and feel of our new CI. I would like to receive proposals of design for a corporate brochure template. I need to receive the Indesign files with full ownership rights to be able to adapt all our documentation with this template.
Regarding the images, you can take gabaris on www.pelvarimages.example. I will be able to take them afterwards.

There will be 4 pages. you will receive the 4 pages on pdf for your consideration with our (almost) actual layout.

- 1st page: cover
- 2nd page: company presentation in french and english
- 3rd page: some market data + graph
- 4th page: 2 retail centers presentation.

In the template, i need to have:
- the paragraph styles in order
- 2 different masters with top/bottom/page number aso.

Please feel free to ask any other questions.

best regards,
Updates

I would like to precise tha t we are active on the commercial real estate sector:

- office transactions (rent /sales)
- property management of administrative and business buildings
- Valuation of properties
- Capital markets (investment advices for selling building)

Industry/Entity Type

Real Estate

Colors

Designer to choose colors to be used in the design.

```html
<!DOCTYPE html>
<html lang="en">
<head>
<meta charset="utf-8">
<title>Altura – Market Data</title>
<link href="https://fonts.googleapis.com/css2?family=Arimo:ital,wght@0,400;0,700;1,400;1,700&display=swap" rel="stylesheet">
<style>
  :root{
    --orange:#f26522;
    --ink:#231f20;
    --text:#3c3c3c;
    --stripe:#f1f1f1;
    --side:#b3b3b4;
    --panel:#eeecec;
    --grid:#9c9c9c;
  }
  *{margin:0;padding:0;box-sizing:border-box}
  html,body{width:873px;height:1200px;overflow:hidden;background:#fff}
  body{position:relative;font-family:"Arimo",Arial,sans-serif;color:var(--text)}
  .page-title{position:absolute;left:95px;top:92px;font-size:19px;font-weight:700;color:var(--orange)}
  .stock-table{position:absolute;left:95px;top:145px;width:480px;border-collapse:collapse;font-size:9px;color:var(--text)}
  .stock-table td,.stock-table th{height:15.5px;padding:0 3px;white-space:nowrap;font-weight:400}
  .stock-table tr:nth-child(odd) td{background:var(--stripe)}
  .stock-table th{background:var(--stripe);font-weight:700;color:var(--ink);text-align:left}
  .stock-table .num{text-align:right}
  .stock-table .c-group{width:160px;font-weight:700;color:var(--ink)}
  .stock-table .c-group.small{font-size:7px}
  .stock-table .c-dist{width:150px}
  .stock-table .c-m2{width:90px}
  .stock-table .c-pct{width:80px;padding-right:12px}
  .stock-table .total td{font-weight:700;font-style:italic;color:var(--ink)}
  .stock-table .total .c-dist{text-align:right}
  .grand-total{position:absolute;left:95px;top:517px;width:480px;height:16px;background:var(--orange);color:#fff;font-size:9px;font-weight:700}
  .grand-total span{position:absolute;top:3px}
  .side-note{position:absolute;left:584px;top:145px;width:201px;height:387px;background:var(--side);color:#fff;padding:18px 15px 0 19px;overflow:hidden}
  .side-note h2{font-size:19px;line-height:22px;font-weight:700;margin-bottom:9px}
  .side-note p{font-size:12.3px;line-height:19.7px;letter-spacing:-0.15px;text-align:justify}
  .side-note p.fr{margin-bottom:22px}
  .caption{position:absolute;left:101px;top:549px;font-size:14px;color:var(--ink)}
  .chart-panel{position:absolute;left:94px;top:595px;width:691px;height:431px;background:var(--panel)}
  .chart-panel svg{position:absolute;left:0;top:0}
  .chart-caption{position:absolute;left:24px;top:400px;font-size:14px;color:var(--ink)}
  .brand{position:absolute;left:72px;top:1090px;font-size:36px;font-weight:700;color:var(--ink);letter-spacing:-1px}
  .footer-rule{position:absolute;left:256px;top:1122px;width:516px;height:1px;background:var(--ink)}
  .page-number{position:absolute;left:781px;top:1112px;font-size:14px;font-weight:700;color:var(--ink)}
</style>
</head>
<body>
  <h1 class="page-title">Lorem Ipsum. Proin gravida nibh vel velit auctor aliquet.</h1>

  <table class="stock-table">
    <tr><th class="c-group"></th><th class="c-dist">QUARTIERS-DISTRICTS</th><th class="c-m2 num">STOCK M²</th><th class="c-pct num" style="padding-right:6px">STOCK %</th></tr>
    <tr><td class="c-group">CENTRE-VILLE (CITY)</td><td class="c-dist">Kirchberg</td><td class="c-m2 num">915 000</td><td class="c-pct num">26,42 %</td></tr>
    <tr><td class="c-group"></td><td class="c-dist">CBD</td><td class="c-m2 num">806 400</td><td class="c-pct num">23,27 %</td></tr>
    <tr><td class="c-group"></td><td class="c-dist">Station</td><td class="c-m2 num">382 700</td><td class="c-pct num">11,04 %</td></tr>
    <tr><td class="c-group"></td><td class="c-dist">Cloche d'Or</td><td class="c-m2 num">365 600</td><td class="c-pct num">10,55 %</td></tr>
    <tr><td class="c-group"></td><td class="c-dist">Limpertsberg</td><td class="c-m2 num">85 000</td><td class="c-pct num">2,45 %</td></tr>
    <tr><td class="c-group"></td><td class="c-dist">Belair / Merl</td><td class="c-m2 num">67 800</td><td class="c-pct num">1,96 %</td></tr>
    <tr><td class="c-group"></td><td class="c-dist">Hamm</td><td class="c-m2 num">44 500</td><td class="c-pct num">1,28 %</td></tr>
    <tr><td class="c-group"></td><td class="c-dist">Kalchesbrück</td><td class="c-m2 num">33 000</td><td class="c-pct num">0,95 %</td></tr>
    <tr class="total"><td class="c-group"></td><td class="c-dist">TOTAL2</td><td class="c-m2 num">700 500</td><td class="c-pct num">77,92 %</td></tr>
    <tr><td class="c-group small">VILLE-PÉRIPHÉRIE (CITY-PERIPHERY)</td><td class="c-dist">Airport - Findel</td><td class="c-m2 num">157 500</td><td class="c-pct num">4,54 %</td></tr>
    <tr><td class="c-group"></td><td class="c-dist">Bertrange / Bourmicht</td><td class="c-m2 num">82 000</td><td class="c-pct num">2,37 %</td></tr>
    <tr><td class="c-group"></td><td class="c-dist">Strassen</td><td class="c-m2 num">81 050</td><td class="c-pct num">2,34 %</td></tr>
    <tr><td class="c-group"></td><td class="c-dist">Howald</td><td class="c-m2 num">62 600</td><td class="c-pct num">1,81 %</td></tr>
    <tr class="total"><td class="c-group"></td><td class="c-dist">TOTAL</td><td class="c-m2 num">383 150</td><td class="c-pct num">11,06 %</td></tr>
    <tr><td class="c-group">PÉRIPHÉRIE (PERIPHERY)</td><td class="c-dist">Belval</td><td class="c-m2 num">93 090</td><td class="c-pct num">2,69 %</td></tr>
    <tr><td class="c-group"></td><td class="c-dist">Capellen</td><td class="c-m2 num">69 500</td><td class="c-pct num">2,01 %</td></tr>
    <tr><td class="c-group"></td><td class="c-dist">Leudelange</td><td class="c-m2 num">73 556</td><td class="c-pct num">2,12 %</td></tr>
    <tr><td class="c-group"></td><td class="c-dist">Munsbach</td><td class="c-m2 num">60 100</td><td class="c-pct num">1,73 %</td></tr>
    <tr><td class="c-group"></td><td class="c-dist">Windhof</td><td class="c-m2 num">40 600</td><td class="c-pct num">1,17 %</td></tr>
    <tr><td class="c-group"></td><td class="c-dist">Esch-sur-Alzette</td><td class="c-m2 num">24 700</td><td class="c-pct num">0,71 %</td></tr>
    <tr><td class="c-group"></td><td class="c-dist">Contern</td><td class="c-m2 num">20 400</td><td class="c-pct num">0,59 %</td></tr>
    <tr class="total"><td class="c-group"></td><td class="c-dist">TOTAL</td><td class="c-m2 num">381 946</td><td class="c-pct num">11,02 %</td></tr>
  </table>

  <div class="grand-total"><span style="left:164px">TOTAL3</span><span style="left:362px">465 596</span></div>

  <aside class="side-note">
    <h2>STOCK</h2>
    <p class="fr">Le stock de mètres carrés disponibles de bureaux a augmenté de 0,36&nbsp;% au troisième trimestre de cette année grâce à la livraison de près de 12&nbsp;300&nbsp;m². Le stock total équivaut à 3&nbsp;465&nbsp;600&nbsp;m².</p>
    <h2>STOCK</h2>
    <p>The stock of available office square meters has increased by 0.36% during the third quarter of this year with the delivery of 12,300&nbsp;m². The total stock reaches 3,465,600&nbsp;sm².</p>
  </aside>

  <p class="caption">Lorem Ipsum. Proin gravida nibh vel aliquet.</p>

  <section class="chart-panel">
    <svg width="691" height="431" viewBox="94 595 691 431" font-family="Arimo, Arial, sans-serif">
      <rect x="116" y="620" width="647" height="340" fill="#fff"/>
      <text x="444" y="667" font-size="18" fill="#231f20" text-anchor="middle">Lorem Ipsum. Proin gravida nibh vel aliquet.</text>
      <text x="137" y="664" font-size="9" font-weight="700" fill="#f26522">000</text>
      <text x="137" y="675" font-size="9" font-weight="700" fill="#f26522">m²</text>
      <g stroke="#9c9c9c" stroke-width="1">
        <line x1="174" y1="708" x2="722" y2="708"/>
        <line x1="174" y1="746" x2="722" y2="746"/>
        <line x1="174" y1="784" x2="722" y2="784"/>
        <line x1="174" y1="821" x2="722" y2="821"/>
        <line x1="174" y1="859" x2="722" y2="859"/>
        <line x1="174" y1="897" x2="722" y2="897"/>
        <line x1="174" y1="934" x2="722" y2="934"/>
      </g>
      <g font-size="13" fill="#3c3c3c">
        <text x="133" y="712">3.500</text>
        <text x="133" y="750">3.200</text>
        <text x="133" y="788">2.900</text>
        <text x="133" y="825">2.600</text>
        <text x="133" y="863">2.300</text>
        <text x="133" y="901">2.000</text>
        <text x="133" y="938">1.700</text>
      </g>
      <g fill="#f26522">
        <rect x="187" y="876" width="20" height="58"/>
        <rect x="240" y="842" width="20" height="92"/>
        <rect x="293" y="832" width="20" height="102"/>
        <rect x="347" y="822" width="20" height="112"/>
        <rect x="401" y="809" width="20" height="125"/>
        <rect x="455" y="774" width="20" height="160"/>
        <rect x="508" y="754" width="20" height="180"/>
        <rect x="562" y="742" width="20" height="192"/>
        <rect x="616" y="734" width="20" height="200"/>
        <rect x="669" y="725" width="20" height="209"/>
        <rect x="725" y="718" width="20" height="216"/>
      </g>
      <g font-size="9" fill="#3c3c3c" text-anchor="middle">
        <text x="197" y="948">2003</text><text x="250" y="948">2004</text><text x="303" y="948">2005</text>
        <text x="357" y="948">2006</text><text x="411" y="948">2007</text><text x="465" y="948">2008</text>
        <text x="518" y="948">2009</text><text x="572" y="948">2010</text><text x="626" y="948">2011</text>
        <text x="679" y="948">2012</text><text x="735" y="948">YTD 2013</text>
      </g>
      <text x="116" y="971" font-size="7" fill="#3c3c3c">Source: Northgate Market Research</text>
      <line x1="94" y1="985" x2="785" y2="985" stroke="#c9c7c7"/>
      <line x1="672" y1="990" x2="672" y2="1016" stroke="#8a8a8a" stroke-dasharray="1.5 1.5"/>
      <rect x="680" y="995" width="62" height="13" fill="#f26522"/>
      <text x="680" y="1018" font-size="7" fill="#3c3c3c">Stock</text>
    </svg>
    <p class="chart-caption">Lorem Ipsum. Proin gravida nibh vel aliquet.</p>
  </section>

  <div class="brand">ALTURA</div>
  <div class="footer-rule"></div>
  <div class="page-number">03</div>
</body>
</html>
```